RWT Fittings Ltd Business Cards

We need a business card with our business logo. We provide window and door installations on high-rises in west coast British Colombia, Canada.

I would like my business information and details on one side of the card, and the other side the company name with logo

Target Market(s)

General Contractors

Industry/Entity Type

Construction

Contact Information for Business Card

one side i want my company name and logo in the dark theme logo that i provided

Requirements
Must have
• Marco Peltieri, 16045518293, RWTFittings@mailbox-demo.com, 1407-5194 Linden Row Burnaby BC, V5H 2K9, Owner & Manager

```html
<!DOCTYPE html>
<html lang="en">
<head>
<meta charset="utf-8">
<title>RWT Fittings Ltd – Business Card</title>
<link href="https://fonts.googleapis.com/css2?family=Montserrat:wght@600&family=Roboto:wght@400;700&display=swap" rel="stylesheet">
<style>
  :root {
    --page-bg: #d6cec1;
    --card-bg: #ebe5da;
    --card-edge: #f6f2ea;
    --teal: #1f93ad;
    --teal-dark: #1a7f8c;
    --grey: #7a716a;
    --ink: #2c2a28;
  }
  html, body {
    margin: 0;
    padding: 0;
    width: 1200px;
    height: 1046px;
    overflow: hidden;
    background: var(--page-bg);
  }
  .canvas {
    position: relative;
    width: 1200px;
    height: 1046px;
  }
  .card {
    position: absolute;
    left: 50px;
    top: 223px;
    width: 1100px;
    height: 600px;
    background: var(--card-bg);
    border: 2px solid var(--card-edge);
    border-radius: 30px;
    box-sizing: border-box;
    overflow: hidden;
    font-family: "Roboto", Arial, sans-serif;
    color: var(--ink);
  }
  .name-bar {
    position: absolute;
    left: 0;
    top: 290px;
    width: 22px;
    height: 86px;
    background: var(--teal-dark);
  }
  .name {
    position: absolute;
    left: 38px;
    top: 282px;
    margin: 0;
    font-weight: 700;
    font-size: 52px;
    line-height: 60px;
    letter-spacing: -0.5px;
  }
  .name .first { color: var(--teal-dark); }
  .name .last { color: var(--grey); }
  .role {
    position: absolute;
    left: 40px;
    top: 344px;
    margin: 0;
    font-family: "Montserrat", Arial, sans-serif;
    font-weight: 600;
    font-size: 23px;
    color: var(--ink);
  }
  .address {
    position: absolute;
    left: 40px;
    top: 398px;
    margin: 0;
    font-style: normal;
    font-size: 26px;
    line-height: 34px;
    letter-spacing: 0.3px;
  }
  .contact {
    position: absolute;
    left: 38px;
    top: 486px;
    margin: 0;
    padding: 0;
    list-style: none;
    font-size: 26px;
    line-height: 34px;
    letter-spacing: 0.3px;
  }
  .contact li {
    display: flex;
    align-items: center;
    gap: 22px;
  }
  .contact svg { width: 22px; height: 22px; fill: var(--teal-dark); }
  .brand-name {
    position: absolute;
    right: 48px;
    top: 40px;
    height: 480px;
    margin: 0;
    writing-mode: vertical-rl;
    transform: rotate(180deg);
    text-align: center;
    font-family: "Roboto", Arial, sans-serif;
    font-weight: 700;
    font-size: 62px;
    line-height: 1;
    color: var(--teal);
    white-space: nowrap;
  }
</style>
</head>
<body>
<main class="canvas">
  <section class="card" aria-label="RWT Fittings Ltd business card">
    <div class="name-bar"></div>
    <h1 class="name"><span class="first">Marco</span> <span class="last">Peltieri</span></h1>
    <p class="role">Owner &amp; Manager</p>
    <address class="address">1407-5194 Linden Row<br>Burnaby BC, V5H 2K9</address>
    <ul class="contact">
      <li>
        <svg viewBox="0 0 24 24" aria-hidden="true"><path d="M6.6 10.8a15.1 15.1 0 0 0 6.6 6.6l2.2-2.2a1 1 0 0 1 1-.25 11.4 11.4 0 0 0 3.6.57 1 1 0 0 1 1 1V20a1 1 0 0 1-1 1A17 17 0 0 1 3 4a1 1 0 0 1 1-1h3.5a1 1 0 0 1 1 1c0 1.25.2 2.45.57 3.57a1 1 0 0 1-.25 1z"/></svg>
        <span>1604 551 8293</span>
      </li>
      <li>
        <svg viewBox="0 0 24 24" aria-hidden="true"><path d="M2 9l10-7 10 7v12H2zm2 1.2V19h16v-8.8l-8 5.6z"/></svg>
        <span>RWTFittings@mailbox-demo.com</span>
      </li>
    </ul>
    <p class="brand-name">RWT Fittings Ltd</p>
  </section>
</main>
</body>
</html>
```